Prayer Service 12.28.2013

I need a flyer designed for a Christian prayer service. The title and theme is:
"Total and Complete Surrender for Total and Complete Deliverance!"
1. You have creative freedom with imagery and typography
2. I need a quick turnaround time
FLYER DETAILS:
A prayer, anointing, and deliverance all night prayer service, at Valleybrook Assembly.
Saturday December 28 2013 from 9pm-6am.
Special guest speakers, prayer,anointing,and deliverance sessions.
For more information contact Sis Rosalind Okafor at Valleybrook Assembly 347 562 9140 Ext. 4816 or Marlene Cobb at 631 208-4392

```html
<!DOCTYPE html>
<html lang="en">
<head>
<meta charset="UTF-8">
<title>Total and Complete Surrender – All Night Prayer Service</title>
<link rel="stylesheet" href="https://fonts.googleapis.com/css2?family=Arimo:wght@700&display=swap">
<style>
  :root {
    --ink-black: #000000;
    --text-white: #ffffff;
    --sky-dark: #2c2d33;
    --sky-mid: #6d6a70;
    --sky-cloud: #8a7f80;
    --sun-core: #fff8ee;
    --sun-warm: #e7b49a;
    --field-dark: #1d1f16;
    --field-olive: #4a4a2c;
  }
  html, body {
    margin: 0;
    padding: 0;
    overflow: hidden;
    background: var(--ink-black);
  }
  .flyer {
    position: relative;
    width: 834px;
    height: 1200px;
    overflow: hidden;
    font-family: "Arimo", Arial, sans-serif;
    font-weight: 700;
    color: var(--text-white);
    background: var(--sky-dark);
  }
  .hero-photo {
    position: absolute;
    inset: 0;
    background:
      radial-gradient(circle at 572px 620px, var(--sun-core) 0, var(--sun-core) 40px, rgba(240,190,160,0.85) 90px, rgba(190,140,130,0.45) 200px, rgba(120,100,105,0) 380px),
      linear-gradient(to bottom, rgba(0,0,0,0) 860px, var(--field-olive) 960px, var(--field-dark) 1200px),
      linear-gradient(to bottom, var(--sky-dark) 0, var(--sky-mid) 320px, var(--sky-cloud) 620px, #5b5255 860px);
  }
  .figure-silhouette {
    position: absolute;
    left: 0;
    top: 360px;
    width: 290px;
    height: 840px;
    background: linear-gradient(to bottom, rgba(30,24,22,0.75), rgba(25,25,20,0.9));
    border-radius: 140px 120px 0 0;
  }
  .title-band {
    position: absolute;
    left: 0; top: 0;
    width: 834px;
    height: 240px;
    background: linear-gradient(to bottom, var(--ink-black) 0, var(--ink-black) 190px, rgba(0,0,0,0) 240px);
  }
  .event-title {
    position: absolute;
    left: 81px;
    top: 100px;
    margin: 0;
    font-size: 59px;
    line-height: 72px;
    letter-spacing: -0.3px;
  }
  .event-summary {
    position: absolute;
    left: 283px;
    top: 366px;
    width: 500px;
    margin: 0;
    font-size: 23px;
    line-height: 31px;
  }
  .event-schedule {
    position: absolute;
    left: 300px;
    top: 928px;
    width: 480px;
    margin: 0;
    text-align: center;
    font-size: 23px;
    line-height: 31px;
  }
  .event-contact {
    position: absolute;
    left: 283px;
    top: 1078px;
    width: 500px;
    margin: 0;
    font-size: 14.5px;
    line-height: 19px;
  }
</style>
</head>
<body>
<main class="flyer">
  <div class="hero-photo" role="img" aria-label="A man kneeling in a grassy field with hands clasped in prayer beneath a cloudy sky lit by a bright setting sun">
    <div class="figure-silhouette"></div>
  </div>
  <div class="title-band"></div>

  <h1 class="event-title">" Total and Complete<br>Surrender for Total and<br>Complete Deliverance! "</h1>

  <p class="event-summary">A prayer, anointing, and deliverance all night prayer service, at Valleybrook Assembly.</p>

  <p class="event-schedule">Saturday / December 28 2013<br>from 9pm-6am.<br>Special guest speakers, prayer,anoint-<br>ing,and deliverance sessions.</p>

  <p class="event-contact">For more information contact Sis Rosalind Okafor at Valley-<br>brook Assembly 347 562 9140 Ext. 4816 or Marlene Cobb<br>at 631 208-4392</p>
</main>
</body>
</html>
```